Website for a financial survey consultancy

WHO WE ARE
We're a niche HR consultancy specialising in salary comparison surveys for the financial asset management industry. We position ourselves as a small, highly responsive organisation with a strong personal relationship with each of our 50+ blue-chip clients.

WHAT WE DO
Our business is 80% surveys (= products), 20% consultancy (= services). The surveys are a set of online products which clients interact with to find the information they are interested in.

WHAT WE WANT
We are completely revising our existing marketing website and need a new up-to-date look and feel for the site. We want you to design 2 web pages
- Home page
- Internal content page

More details below in Must Have Priorities.

REFERENCE SITES
- www.veltramoor.com - nice background image
- www.plimweather.com - ignoring the animations
- www.gasketvale.com
- www.quorbin.com - clean, fresh, styly but prob not corporate enough
- www.dulveropinex.com - spacious, beautiful, slightly dated tho
- www.tambly.co.uk - ignore the colours. Like the simplicity, larger font size (although want to stick with sans-serif fonts for main content)

DELIVERABLES
The final designs should be delivered as one or more PSD files with clearly named layers. All design elements and treatments should be separated out, for example use adjustment layers rather than applied (and subsequently irreversible) adjustments, strokes, shading, etc.

WHAT NEXT
I'll be monitoring the contest every day and can respond to questions fast. You can IM me on Chatterlyne or QBX.

Reason: Hi folks,

I am extending the deadline to this project as I am travelling this week and therefore will not be able to make a final decision until next Monday. I will try and provide further feedback over the course of this week but I am only going to be online occasionally so be prepared to wait a few days for a reply from me.

Thanks for all the designs so far.

Tobias

Target Market(s)

In order of importance, most important first

1. Potential customers - UK & US financial industry HR professionals, short on time. Heard about us already, want to find out more about what we do, confirm relevance for their needs. Core goal - establish credibility: are we properly resourced, will we be around for years to come, are we *real*.

2. Existing customers - UK & US financial industry professionals, short on time, under pressure, want results quickly, minimum faff, expect high quality, slickly presented information. Primary action: login and use surveys.

3. Industry professionals/researchers - probably arriving through blog content, looking to browse and hoover information. Valuable for their ability to spread awareness of who we are amongst their peers.

Industry/Entity Type

Financial

Requirements
Must have
• GENERAL
Style cues - Corporate, professional, financial, stylish, slick, clean, spacious, light
Size - standard 960px grid

NAVIGATION
- [ Home | About us | Surveys | Consulting | Blog ]
- Sub-nav (roll-over dropdown) on About Us, Surveys & Consulting

ALL PAGES
- Site navigation
- Client login (on screen permanently or link to ajaxy in-page pop-up)
- Footer section
- Existing logo (attached)* - this is obviously an important reference point in the design, esp colour

HOME PAGE
- Communicate (link thru to?) survey/consulting split
- Large photo(s)/backdrop (2-3 interchangeable options ideally). Please consider what rights agreement will be necessary for any photos you include in your design.
- Possibly bigger more prominent version of logo
- Strap line/sentence - "Focussed data is the key to success"
- 3 recent blog posts (should look good with and without blog post images)
- Free downloadable PDF research report + supporting blurb

INTERNAL PAGE
- Page title
- Content - typical page will be less than one screenfull
- Level 1 sub-heading
- Level 2 sub-heading
- Bulleted list
- Content supporting image (any image will do - interested in placement, borders (if any), spacing, caption, etc)
- 'Do something' button

* Note: there is some internal debate about this logo at the moment. Some (me) are keen for it to change, some (not me!) are not. If you have an web page design idea/concept that requires an evolution of the logo, go ahead and evolve it. We can explore this further in the design process as necessary, but don't sweat it.
Nice to have
• Values to communicate
- Knowledgeable
- Professional
- Secure
- Personal
- Experienced
- Financial industry specific
- Accurate
- Reliable
Should not have
• - Search box
- Social media links, other than RSS feed button (discrete)

```html
<!DOCTYPE html>
<html lang="en">
<head>
<meta charset="utf-8">
<title>Corvia — HR consultancy</title>
<link rel="stylesheet" href="https://fonts.googleapis.com/css2?family=Arimo:wght@400;700&family=Roboto+Condensed:wght@300;400&display=swap">
<style>
:root{
  --stage:#333333;
  --sky-top:#4f8fe6;
  --sky-mid:#8fbdf0;
  --sky-low:#cfe3f3;
  --column-veil:rgba(255,255,255,0.86);
  --nav-top:#4a5358;
  --nav-bottom:#2c3438;
  --login-bg:#6b98cc;
  --login-title:#f2ea3a;
  --intro-bg:rgba(28,42,50,0.94);
  --intro-accent:#5d90e6;
  --footer-bg:#060b10;
  --footer-text:#c9cdd1;
  --footer-muted:#9aa0a6;
  --blog-text:#2a2a2a;
  --read-more:#e0531b;
  --white:#ffffff;
}
*{box-sizing:border-box;margin:0;padding:0}
html,body{width:1200px;height:900px;overflow:hidden;background:var(--stage)}
body{position:relative;font-family:Arimo,Arial,sans-serif}
.site{position:absolute;left:121px;top:69px;width:964px;height:757px;overflow:hidden}
.hero-backdrop{position:absolute;left:0;top:0;width:964px;height:674px;
  background:
    linear-gradient(160deg,rgba(40,50,70,0.55) 0%,rgba(40,50,70,0.2) 35%,transparent 55%),
    linear-gradient(180deg,transparent 80%,rgba(120,130,140,0.6) 100%),
    linear-gradient(180deg,var(--sky-top) 0%,var(--sky-mid) 55%,var(--sky-low) 100%)}
.sidebar-veil{position:absolute;left:670px;top:0;width:261px;height:674px;background:var(--column-veil)}
.brand{position:absolute;left:28px;top:44px;display:flex;align-items:center;gap:10px;text-decoration:none}
.brand-dot{display:block;width:16px;height:16px;background:var(--white)}
.brand-name{color:var(--white);font-family:Arimo,Arial,sans-serif;font-size:34px;font-weight:400;line-height:1}
.main-nav{position:absolute;left:475px;top:92px;width:477px;height:48px;
  background:linear-gradient(180deg,var(--nav-top),var(--nav-bottom));
  display:flex;align-items:center;justify-content:center}
.main-nav a{color:var(--white);text-decoration:none;font-size:12px;padding:0 20px;white-space:nowrap}
.main-nav .sep{color:var(--white);font-size:12px}
.client-login{position:absolute;left:678px;top:146px;width:247px;height:179px;background:var(--login-bg);padding:14px 8px 0}
.client-login h2{color:var(--login-title);font-size:14px;font-weight:700}
.client-login label{display:block;color:var(--white);font-size:12px;margin-top:8px}
.client-login label:first-of-type{margin-top:9px}
.client-login .field{display:block;width:225px;height:22px;background:var(--white);border:0;margin-top:3px}
.login-actions{display:flex;align-items:center;margin-top:11px;gap:5px}
.login-button{width:72px;height:26px;border-radius:5px;background:linear-gradient(180deg,#ffffff,#dde3ea);border:1px solid #b7c3d0;color:#2a4f8a;font-size:11px;font-family:inherit;letter-spacing:0.5px}
.forgot{color:#e9f1fb;font-size:11px;font-weight:700;text-decoration:none}
.latest-blogs{position:absolute;left:685px;top:356px;width:240px}
.latest-blogs h2{font-family:"Roboto Condensed","Arial Narrow",sans-serif;font-weight:400;font-size:22px;color:#111;margin-left:3px}
.blog-post{display:flex;gap:8px;margin-top:16px}
.blog-post:first-of-type{margin-top:14px}
.blog-post+.blog-post{margin-top:20px}
.blog-thumb{flex:none;width:53px;height:53px;border:3px solid #9a9a9a;background:linear-gradient(160deg,#d8d2cb,#8e8378)}
.blog-body{width:168px}
.blog-body p{font-size:11px;font-weight:700;color:var(--blog-text);line-height:13.5px}
.read-more{display:inline-block;margin-top:6px;margin-left:2px;color:#111;font-size:11px;text-decoration:underline}
.read-more span{color:var(--read-more);font-weight:700;margin-left:3px;font-size:13px}
.read-more.tight{margin-top:0}
.intro{position:absolute;left:25px;top:258px;width:443px;height:302px;background:var(--intro-bg);padding:16px 22px 0 19px}
.intro h1{font-family:"Roboto Condensed","Arial Narrow",sans-serif;font-weight:300;font-size:67px;line-height:72px;color:var(--white);letter-spacing:-0.5px}
.intro .strap{font-family:"Roboto Condensed","Arial Narrow",sans-serif;font-weight:400;font-size:21.5px;line-height:29px;color:var(--intro-accent);margin-top:2px}
.intro .lead{font-size:12.5px;line-height:14.7px;letter-spacing:0.5px;word-spacing:0.5px;color:var(--white);text-align:justify;hyphens:auto;-webkit-hyphens:auto;margin-top:15px;padding-left:5px}
.site-footer{position:absolute;left:0;top:674px;width:964px;height:83px;background:var(--footer-bg)}
.footer-nav{position:absolute;left:24px;top:26px;display:flex;font-size:12px;color:var(--footer-text)}
.footer-nav a{color:var(--footer-text);text-decoration:none}
.footer-nav .sep{padding:0 23px}
.copyright{position:absolute;left:24px;top:44px;font-size:11px;color:var(--footer-muted)}
.footer-brand{position:absolute;right:33px;top:30px;display:flex;align-items:center;gap:6px}
.footer-brand .brand-dot{width:9px;height:9px}
.footer-brand .brand-name{font-size:15px}
</style>
</head>
<body>
<div class="site">
  <div class="hero-backdrop" role="img" aria-label="Photograph of a long concrete road bridge curving across a bay under a clear blue sky"></div>
  <div class="sidebar-veil"></div>

  <a class="brand" href="#">
    <span class="brand-dot"></span>
    <span class="brand-name">Corvia</span>
  </a>

  <nav class="main-nav">
    <a href="#">HOME</a><span class="sep">|</span>
    <a href="#">ABOUT US</a><span class="sep">|</span>
    <a href="#">SURVEYS</a><span class="sep">|</span>
    <a href="#">CONSULTING</a><span class="sep">|</span>
    <a href="#">BLOG</a>
  </nav>

  <form class="client-login">
    <h2>Client LOGIN</h2>
    <label for="user">User Name</label>
    <input class="field" id="user" type="text">
    <label for="pass">Password</label>
    <input class="field" id="pass" type="password">
    <div class="login-actions">
      <button class="login-button" type="button">LOGIN ››</button>
      <a class="forgot" href="#">Forgot Password?</a>
    </div>
  </form>

  <section class="latest-blogs">
    <h2>Latest Blogs</h2>
    <article class="blog-post">
      <div class="blog-thumb" role="img" aria-label="Author portrait"></div>
      <div class="blog-body">
        <p>Lorem ipsum dolor sit amet, consectetur adipiscing elit. Cras ante du</p>
        <a class="read-more" href="#">Read More<span>»</span></a>
      </div>
    </article>
    <article class="blog-post">
      <div class="blog-thumb" role="img" aria-label="Author portrait"></div>
      <div class="blog-body">
        <p>Lorem ipsum dolor sit amet, consectetur adipiscing elit. Cras ante du</p>
        <a class="read-more" href="#">Read More<span>»</span></a>
      </div>
    </article>
    <article class="blog-post">
      <div class="blog-thumb" role="img" aria-label="Author portrait"></div>
      <div class="blog-body">
        <p>Lorem ipsum dolor sit amet, consectetur adipiscing elit. Cras ante du</p>
        <a class="read-more tight" href="#">Read More<span>»</span></a>
      </div>
    </article>
  </section>

  <section class="intro" lang="en">
    <h1>HR consultancy</h1>
    <p class="strap">specialising in salary comparison surveys for the financial asset management industry</p>
    <p class="lead">Lorem ipsum dolor sit amet, consectetur adipiscing elit. Cras ante dui, viverra non vehicula in, condimentum id ipsum. Fusce at arcu metus. Fusce eu justo nisl. Maecenas consequat condi&shy;mentum ante, quis tincidunt neque viverra sed. Aenean tempus rhoncus dolor, at dapibus ipsum dapibus at. Nulla ac turpis a quam venenatis molestie sit amet ut enim. Sed elementum feu&shy;giat bibendum. Morbi sed adipiscing tellus.</p>
  </section>

  <footer class="site-footer">
    <nav class="footer-nav">
      <a href="#">Home</a><span class="sep">|</span>
      <a href="#">about us</a><span class="sep">|</span>
      <a href="#">Surveys</a><span class="sep">|</span>
      <a href="#">Consulting</a><span class="sep">|</span>
      <a href="#">Blog</a>
    </nav>
    <p class="copyright">© 2011 Corvia. All rights reserved</p>
    <div class="footer-brand">
      <span class="brand-dot"></span>
      <span class="brand-name">Corvia</span>
    </div>
  </footer>
</div>
</body>
</html>
```